NZ First of it's kind solutions directory and marketplace for busy Mums needs a business card design

We need a business card design for our new nationwide business in NZ (long term plans to go global). We provide solutions to the everyday challenges that busy Mums face by connecting them with quality communities and suppliers of carefully selected, relevant products and services. We sell direct via our online marketplace. The final design should communicate our values of inclusivity, quality and smart solutions. Colours should incorporate our logo colour palette of #477077 and #6ba8b2. Our website is at https://www.brightnestmums.example

Target Market(s)

busy Mums, Age 28 – 50, female, income over $100K, location main centres NZ primarily but NZ wide. Is likely juggling work or career with a young family. Probably had hobbies which have fallen by the wayside.
-Wants to succeed in her chosen career without compromising on family life
-to successfully juggle her career without feeling like she is compromising her children
- Is time poor, something always has to give and it’s generally her health (she’ll stay up late, get stressed)
- probably ex corporate or professional career. Has discretional income

Industry/Entity Type

Business

Contact Information for Business Card

Lena Forbisher, Founder, BrightNestMums.example (Strapline Tap; Gather; Sorted), 47 Kowhai Terrace, Ellerslie, Auckland 1051, New Zealand. Mob: 021 483 517 Ph: +64 (0)9 571 4860

Font styles to use
Other font styles liked:
• Raleway, and/or Architects Daughter

Colors
00a990
33b8a4
86cfc6
cfeae6

Requirements
Must have
• the above details, streamline. the logo and colours associated with those logos
Should not have
• foil or metallic colours

```html
<!DOCTYPE html>
<html lang="en">
<head>
<meta charset="utf-8">
<title>BrightNestMums — Business Card</title>
<link rel="stylesheet" href="https://fonts.googleapis.com/css2?family=Roboto+Condensed:wght@400;700&family=Roboto:wght@400;500&display=swap">
<style>
  :root {
    --backdrop: #262626;
    --card-white: #f2f2f1;
    --brand-dark: #477077;
    --brand-light: #6ba8b2;
    --brand-teal: #00aa8f;
    --text-grey: #555a5c;
    --rule-grey: #b5b8b8;
    --white: #ffffff;
  }
  * { margin: 0; padding: 0; box-sizing: border-box; }
  html, body {
    width: 1200px; height: 960px; overflow: hidden;
    background: var(--backdrop);
  }
  .canvas { position: relative; width: 1200px; height: 960px; }

  .card {
    position: absolute; width: 600px; height: 343px;
    border-radius: 22px; overflow: hidden;
    box-shadow: 0 3px 6px rgba(0,0,0,0.45);
  }
  .card--front { left: 314px; top: 113px; background: var(--card-white); }
  .card--back { left: 311px; top: 472px; background: var(--brand-teal); }

  .wordmark {
    position: absolute; display: flex; align-items: center; gap: 10px;
    font-family: "Roboto Condensed", sans-serif; font-weight: 700;
    letter-spacing: -0.5px; white-space: nowrap;
  }
  .wordmark__dot { border-radius: 50%; flex: none; }
  .card--front .wordmark {
    right: 36px; top: 52px; font-size: 36px; color: var(--brand-dark);
  }
  .card--front .wordmark__dot { width: 20px; height: 20px; background: var(--brand-dark); }
  .card--back .wordmark {
    left: 0; right: 0; justify-content: center; top: 146px;
    font-size: 44px; color: var(--white);
  }
  .card--back .wordmark__dot { width: 24px; height: 24px; background: var(--white); }

  .name-accent {
    position: absolute; left: 0; top: 195px; width: 14px; height: 39px;
    background: var(--brand-dark);
  }
  .holder { position: absolute; left: 36px; top: 193px; }
  .holder__name {
    font-family: "Roboto Condensed", sans-serif; font-weight: 700;
    font-size: 22px; color: var(--brand-dark); line-height: 1.1;
  }
  .holder__role {
    font-family: "Roboto Condensed", sans-serif; font-weight: 400;
    font-size: 16px; color: var(--brand-light); letter-spacing: 0.5px;
    margin-left: 2px; line-height: 1.2;
  }
  .rule {
    position: absolute; left: 36px; top: 243px; width: 527px; height: 1px;
    background: var(--rule-grey);
  }
  .contacts {
    position: absolute; left: 36px; top: 254px; list-style: none;
    font-family: "Roboto", sans-serif; font-size: 14.5px; color: var(--text-grey);
  }
  .contacts li { display: flex; align-items: center; gap: 8px; height: 19px; }
  .contacts svg { width: 13px; height: 13px; fill: var(--brand-dark); flex: none; }
  .address {
    position: absolute; right: 35px; top: 273px; text-align: right;
    font-family: "Roboto", sans-serif; font-size: 14.5px; color: var(--text-grey);
    line-height: 19px; font-style: normal;
  }

  .strapline {
    position: absolute; left: 0; right: 0; top: 284px; text-align: center;
    font-family: "Roboto", sans-serif; font-size: 14.5px; color: var(--white);
  }
</style>
</head>
<body>
<main class="canvas">
  <section class="card card--front" aria-label="Business card front">
    <div class="wordmark"><span class="wordmark__dot"></span>BrightNestMums</div>

    <span class="name-accent"></span>
    <div class="holder">
      <p class="holder__name">LENA FORBISHER</p>
      <p class="holder__role">FOUNDER</p>
    </div>
    <span class="rule"></span>

    <ul class="contacts">
      <li>
        <svg viewBox="0 0 24 24" aria-hidden="true"><path d="M6.6 10.8a15.1 15.1 0 0 0 6.6 6.6l2.2-2.2c.3-.3.7-.4 1-.2 1.1.4 2.3.6 3.6.6.6 0 1 .4 1 1V20c0 .6-.4 1-1 1A17 17 0 0 1 3 4c0-.6.4-1 1-1h3.5c.6 0 1 .4 1 1 0 1.3.2 2.5.6 3.6.1.3 0 .7-.2 1z"/></svg>
        +64 (0)9 571 4860
      </li>
      <li>
        <svg viewBox="0 0 24 24" aria-hidden="true"><path d="M7 1h10a2 2 0 0 1 2 2v18a2 2 0 0 1-2 2H7a2 2 0 0 1-2-2V3a2 2 0 0 1 2-2zm0 3v14h10V4zm5 15.5a1.2 1.2 0 1 0 0 2.4 1.2 1.2 0 0 0 0-2.4z"/></svg>
        021 483 517
      </li>
      <li>
        <svg viewBox="0 0 24 24" aria-hidden="true"><path d="M12 1a11 11 0 1 0 0 22 11 11 0 0 0 0-22zm-1 19.9A9 9 0 0 1 3.2 10.4L8 15v1a2 2 0 0 0 2 2h1zm6.9-2.5A2 2 0 0 0 16 17h-1v-3a1 1 0 0 0-1-1H8v-2h2a1 1 0 0 0 1-1V8h2a2 2 0 0 0 2-2v-.4a9 9 0 0 1 2.9 12.8z"/></svg>
        BrightNestMums.example
      </li>
    </ul>

    <address class="address">47 Kowhai Terrace, Ellerslie<br>Auckland 1051, New Zealand</address>
  </section>

  <section class="card card--back" aria-label="Business card back">
    <div class="wordmark"><span class="wordmark__dot"></span>BrightNestMums</div>
    <p class="strapline">Tap; Gather; Sorted</p>
  </section>
</main>
</body>
</html>
```